We need a card and logo design for a new business based in Dallas Texas called Stonemarsh Financial LLC.

We provide bridge loans.We offer pay day loans,title loans and check cashing.Our products are emmergency loans that help borrowers meet short term liquidity needs until the next pay check.

The final design should communicate,professionalism,Sophistication and friendliness to our customers.Use the color Blue as much as possible and another eye catching color if possible.We will consider a profesional looking knight logo with the color Blue in it.Please design a full corporate identity.

```html
<!DOCTYPE html>
<html lang="en">
<head>
<meta charset="utf-8">
<title>Stonemarsh Financial LLC – Business Card</title>
<link rel="stylesheet" href="https://fonts.googleapis.com/css2?family=Cinzel:wght@600&family=Open+Sans:wght@400;600&display=swap">
<style>
  :root {
    --stage: #36322f;
    --paper: #ffffff;
    --navy: #1d4a8c;
    --band: #174a8d;
    --ink: #1a1a1a;
    --blue-core: #0b55b0;
    --blue-edge: #223f80;
    --white: #ffffff;
  }
  * { margin: 0; padding: 0; box-sizing: border-box; }
  html, body { width: 1000px; height: 1200px; overflow: hidden; }
  body { background: var(--stage); position: relative; font-family: "Open Sans", sans-serif; }

  .card { position: absolute; left: 139px; width: 723px; height: 422px; }

  /* Front card */
  .card-front { top: 119px; background: var(--paper); }
  .card-front .side-band { position: absolute; right: 0; top: 0; width: 34px; height: 100%; background: var(--band); }
  .card-front .brand-mark {
    position: absolute; left: 118px; top: 176px;
    display: flex; align-items: center; gap: 10px;
    font-family: "Cinzel", serif; font-weight: 600; font-size: 22px;
    color: var(--navy); letter-spacing: 1px;
  }
  .card-front .brand-mark .mark-square { width: 14px; height: 14px; background: var(--navy); }
  .holder { position: absolute; left: 362px; top: 118px; }
  .holder-name { font-family: "Cinzel", serif; font-weight: 600; font-size: 27px; color: var(--navy); letter-spacing: 0.5px; line-height: 1; }
  .holder-title { font-weight: 600; font-size: 18px; color: var(--ink); margin-top: 6px; }
  .contact-list { list-style: none; margin-top: 14px; }
  .contact-list li { display: flex; align-items: flex-start; gap: 9px; font-size: 16px; color: var(--ink); line-height: 22px; margin-bottom: 8px; }
  .contact-list svg { width: 16px; height: 16px; margin-top: 3px; margin-left: 8px; flex: none; fill: var(--navy); }

  /* Back card */
  .card-back {
    top: 637px;
    background: radial-gradient(ellipse at 50% 40%, var(--blue-core) 0%, var(--blue-edge) 75%);
    display: flex; flex-direction: column; align-items: center; justify-content: center;
    color: var(--white); font-family: "Cinzel", serif; font-weight: 600; text-align: center;
  }
  .card-back .mark-circle { width: 22px; height: 22px; border-radius: 50%; background: var(--white); margin-bottom: 22px; margin-top: 40px; }
  .card-back .brand-name { font-size: 44px; letter-spacing: 1px; line-height: 1; }
  .card-back .brand-suffix { font-size: 26px; letter-spacing: 1px; margin-top: 10px; line-height: 1; }
</style>
</head>
<body>
  <section class="card card-front">
    <div class="brand-mark"><span class="mark-square"></span>STONEMARSH</div>
    <div class="holder">
      <h1 class="holder-name">DANIEL REEVE</h1>
      <p class="holder-title">Financial Advisor</p>
      <ul class="contact-list">
        <li><svg viewBox="0 0 16 16" aria-hidden="true"><path d="M3 1l3 3-1.5 2a9 9 0 0 0 5.5 5.5L12 10l3 3-2 2C7 15 1 9 1 3z"/></svg>555-014-2290</li>
        <li><svg viewBox="0 0 16 16" aria-hidden="true"><path d="M4 0h8a1 1 0 0 1 1 1v14a1 1 0 0 1-1 1H4a1 1 0 0 1-1-1V1a1 1 0 0 1 1-1zm1 2v10h6V2zm3 11a1 1 0 1 0 0 2 1 1 0 0 0 0-2z"/></svg>555-014-2291</li>
        <li><svg viewBox="0 0 16 16" aria-hidden="true"><path d="M0 3h16v10H0zm1.5 1.2v.3L8 9l6.5-4.5v-.3zm0 2V12h13V6.2L8 10.5z"/></svg>info@stonemarshfinancial.com</li>
        <li><svg viewBox="0 0 16 16" aria-hidden="true"><path d="M8 0a5.5 5.5 0 0 1 5.5 5.5C13.5 10 8 16 8 16S2.5 10 2.5 5.5A5.5 5.5 0 0 1 8 0zm0 3.5a2 2 0 1 0 0 4 2 2 0 0 0 0-4z"/></svg><span>XXX Some Street Address<br>State, Country</span></li>
      </ul>
    </div>
    <div class="side-band"></div>
  </section>

  <section class="card card-back">
    <span class="mark-circle"></span>
    <p class="brand-name">STONEMARSH</p>
    <p class="brand-suffix">FINANCIAL LLC.</p>
  </section>
</body>
</html>
```